Business Card for a Jewellery Brand

Business card for an upscale jewellery brand. Attached is the brand logo and icon and color board. I am looking for two card versions: one for the founder and one is generic. The card should be elegant and convey upscale and premium feel. I am open to both square and rectangle card shapes.

Industry/Entity Type

Jewelry

Contact Information for Business Card

Two cards: (1) Sunela Parvaniya (Founder) (2) General
(1) Sunela Parvaniya card should have Name: Sunela Parvaniya, Title: Founder Email id: sunela@quiremo.com.au. Phone no: +61452913307
(2) Generic card should have Email id: info@quiremo.com.au. Phone no: +61436207518

Requirements
Must have
• Workmark
• ICON
• Phone no
• Email ID
• ABN: 58219740312 (Note: ABN is Business number in Australia)
• Website: www.quiremo.com.au
• Instagram: quiremo_jewellery
• Facebook: @quiremojewellery
Nice to have
• Tagline

```html
<!DOCTYPE html>
<html lang="en">
<head>
<meta charset="utf-8">
<title>Quiremo Business Card</title>
<link rel="stylesheet" href="https://fonts.googleapis.com/css2?family=Lato:wght@300;400;700&display=swap">
<style>
  :root {
    --rose: #e7999a;
    --rose-deep: #e08f90;
    --white: #ffffff;
    --backdrop: #2b2b2d;
  }
  * { box-sizing: border-box; margin: 0; padding: 0; }
  html, body { width: 1200px; height: 880px; overflow: hidden; }
  body {
    background: var(--backdrop);
    font-family: "Lato", Arial, sans-serif;
    position: relative;
  }
  .card {
    position: absolute;
    width: 600px;
    height: 343px;
    overflow: hidden;
    box-shadow: 0 10px 28px rgba(0,0,0,.45);
  }

  /* Front */
  .card-front { left: 110px; top: 60px; background: var(--rose); }
  .front-pattern {
    position: absolute; inset: 0;
    background: var(--rose-deep);
    opacity: .35;
  }
  .front-content {
    position: relative; height: 100%;
    display: flex; flex-direction: column; align-items: center; justify-content: center;
    color: var(--white);
  }
  .front-wordmark {
    display: flex; align-items: center; gap: 16px;
    font-weight: 300; font-size: 46px; letter-spacing: 10px;
  }
  .mark-dot { width: 22px; height: 22px; border-radius: 50%; background: var(--white); }
  .front-web { margin-top: 34px; font-size: 17px; letter-spacing: 2px; font-weight: 400; }

  /* Back */
  .card-back { left: 490px; top: 470px; background: var(--white); display: flex; }
  .back-brand {
    width: 42%;
    display: flex; align-items: center; justify-content: center; gap: 12px;
    color: var(--rose);
    font-weight: 300; font-size: 34px; letter-spacing: 6px;
  }
  .back-brand .mark-dot { background: var(--rose); width: 16px; height: 16px; }
  .back-info {
    position: relative; flex: 1;
    background: var(--rose);
    color: var(--white);
    padding: 52px 20px 0 50px;
  }
  .divider-line {
    position: absolute; left: 12px; top: 0; bottom: 0;
    width: 4px; background: var(--white);
  }
  .person-name { font-weight: 700; font-size: 20px; letter-spacing: .3px; }
  .person-title { font-weight: 400; font-size: 14px; margin-top: 1px; }
  .contact-list { list-style: none; margin-top: 26px; }
  .contact-item {
    display: flex; align-items: center; gap: 9px;
    font-size: 14px; line-height: 1; margin-bottom: 8px;
  }
  .contact-icon {
    width: 16px; height: 16px; flex: none;
    border: 1.4px solid var(--white); border-radius: 50%;
    display: flex; align-items: center; justify-content: center;
  }
  .contact-icon svg { width: 9px; height: 9px; }
  .abn { margin-top: 24px; font-size: 15px; }
  .abn strong { font-weight: 700; }
</style>
</head>
<body>

  <section class="card card-front" aria-label="Card front">
    <div class="front-pattern" role="img" aria-label="Faint repeating brand pattern"></div>
    <div class="front-content">
      <div class="front-wordmark"><span class="mark-dot"></span>QUIREMO</div>
      <div class="front-web">www.quiremo.com.au</div>
    </div>
  </section>

  <section class="card card-back" aria-label="Card back">
    <div class="back-brand"><span class="mark-dot"></span>QUIREMO</div>
    <div class="back-info">
      <span class="divider-line"></span>
      <div class="person-name">Sunela Parvaniya</div>
      <div class="person-title">Founder</div>
      <ul class="contact-list">
        <li class="contact-item">
          <span class="contact-icon"><svg viewBox="0 0 10 10"><path d="M2 1 L4 1 L4.6 3 L3.4 3.8 Q4.4 5.8 6.2 6.6 L7 5.4 L9 6 L9 8 Q5 9 2 5.5 Q1 3.5 2 1Z" fill="#fff"/></svg></span>
          +61452913307
        </li>
        <li class="contact-item">
          <span class="contact-icon"><svg viewBox="0 0 10 10"><rect x="1" y="2.5" width="8" height="5.5" fill="none" stroke="#fff" stroke-width="1"/><path d="M1 2.5 L5 5.8 L9 2.5" fill="none" stroke="#fff" stroke-width="1"/></svg></span>
          sunela@quiremo.com.au
        </li>
        <li class="contact-item">
          <span class="contact-icon"><svg viewBox="0 0 10 10"><circle cx="5" cy="5" r="4" fill="none" stroke="#fff" stroke-width="1"/><ellipse cx="5" cy="5" rx="1.8" ry="4" fill="none" stroke="#fff" stroke-width=".8"/><path d="M1 5 H9" stroke="#fff" stroke-width=".8"/></svg></span>
          www.quiremo.com.au
        </li>
        <li class="contact-item">
          <span class="contact-icon"></span>
          quiremo_jewellery
        </li>
        <li class="contact-item">
          <span class="contact-icon"></span>
          @quiremojewellery
        </li>
      </ul>
      <div class="abn"><strong>ABN:</strong> 58219740312</div>
    </div>
  </section>

</body>
</html>
```